Quillbrookes websites redesign

Www.quill-brookes.com needs to be redesigned along with updations. The incremental material will be provided for the updations. We are looking for complete redesign of the pages with the new content. The complete write up will be provided soon

Target Market(s)

Global

Coding

Coded - Design and coding required

Number of Pages Required

5+ page

Requirements
Must have
• A clean and slick design for the Consulting.
Should not have
• Too many pictures which reduces the speed of the site

```html
<!DOCTYPE html>
<html lang="en">
<head>
<meta charset="utf-8">
<title>Quillbrookes Consultancy</title>
<link href="https://fonts.googleapis.com/css2?family=Open+Sans:wght@400;600&family=Roboto:wght@300;400;500;700&display=swap" rel="stylesheet">
<style>
:root{
  --blue:#2f9bd3;
  --blue-panel:#39a6d6;
  --maroon:#6e2424;
  --ink:#333;
  --text:#666;
  --muted:#888;
  --light:#f3f3f3;
  --red-date:#b03a2e;
  --footer:#2b2b2b;
  --white:#fff;
}
*{box-sizing:border-box;margin:0;padding:0}
html,body{width:1200px;height:2390px;overflow:hidden;background:var(--white)}
body{position:relative;font-family:"Open Sans",Arial,sans-serif;color:var(--text)}
.abs{position:absolute}

/* header */
.site-header{left:0;top:0;width:1200px;height:96px;background:var(--white)}
.brand{left:99px;top:26px;display:flex;align-items:center;gap:10px}
.brand-dot{width:40px;height:40px;border-radius:50%;background:var(--maroon)}
.brand-name{font-family:"Roboto",sans-serif;font-size:30px;font-weight:400;color:var(--maroon)}
.main-nav{right:98px;top:38px;display:flex;gap:38px;font-family:"Roboto",sans-serif;font-size:13px;color:var(--ink);letter-spacing:.3px}
.main-nav .active{color:var(--blue);border-bottom:1px solid var(--blue);padding-bottom:4px}

/* hero */
.hero{left:0;top:96px;width:1200px;height:558px;background:linear-gradient(180deg,#3f5680 0%,#6a6f9a 28%,#52628c 48%,#2a3b5b 62%,#1b2c45 80%,#14253a 100%)}
.hero-title{left:0;width:1200px;top:228px;text-align:center;font-family:"Roboto",sans-serif;font-weight:700;font-size:46px;color:#fff;text-shadow:0 2px 4px rgba(0,0,0,.5)}
.hero-sub{left:0;width:1200px;top:282px;text-align:center;font-family:"Roboto",sans-serif;font-weight:300;font-size:31px;color:#fff;text-shadow:0 2px 4px rgba(0,0,0,.5)}
.hero-arrow{top:250px}

/* service panels */
.panel{top:654px;height:243px;color:#fff}
.panel-left{left:0;width:599px;background:var(--blue-panel)}
.panel-right{left:599px;width:601px;background:var(--maroon)}
.panel h3{position:absolute;font-family:"Roboto",sans-serif;font-weight:400;font-size:19px;line-height:26px;text-transform:uppercase}
.panel p{position:absolute;font-size:11.5px;line-height:21px;color:#eef}
.panel-left h3{left:175px;top:43px}
.panel-left p{left:99px;top:105px;width:445px}
.panel-right h3{left:150px;top:43px}
.panel-right p{left:74px;top:105px;width:450px}
.panel-icon{position:absolute;top:40px}
.center-badge{left:553px;top:730px;width:94px;height:94px;border-radius:50%;background:#fff;border:3px solid var(--maroon)}

/* welcome */
.video{left:99px;top:963px;width:483px;height:301px;background:linear-gradient(160deg,#2e3c78 0%,#4a3f6e 45%,#6b3a3a 75%,#2d2530 100%);border:2px solid #3a4a8a}
.play{left:315px;top:1083px;width:52px;height:34px;background:#111;border-radius:6px}
.welcome-title{left:615px;top:968px;font-family:"Roboto",sans-serif;font-size:30px;font-weight:300;color:var(--ink)}
.welcome-title span{color:var(--blue)}
.welcome-text{left:615px;top:1015px;width:487px;font-size:11.2px;line-height:20.5px;text-align:justify}
.welcome-text p{margin-bottom:14px}

/* case studies */
.cases{left:0;top:1339px;width:1200px;height:470px;background:var(--light);border-top:1px solid #e6e6e6;border-bottom:1px solid #e6e6e6}
.cases-title{left:0;width:1200px;top:1388px;text-align:center;font-family:"Roboto",sans-serif;font-size:32px;color:var(--ink)}
.cases-intro{left:220px;width:760px;top:1436px;text-align:center;font-size:11.5px;line-height:21px;color:var(--text)}
.case{top:1527px;width:244px;height:222px}
.case-label{position:absolute;left:20px;top:141px;background:#fff;color:#555;font-family:"Roboto",sans-serif;font-size:13px;padding:6px 11px;text-transform:uppercase}
.case-tag{position:absolute;left:20px;top:182px;background:var(--blue);color:#fff;font-size:12px;padding:4px 10px}
.case-arrow{top:1594px}

/* news */
.news-head{left:99px;top:1858px;display:flex;align-items:center;gap:12px;font-family:"Roboto",sans-serif;font-size:26px;color:var(--ink)}
.news-dot{width:28px;height:28px;border-radius:50%;background:var(--maroon)}
.news-item{left:99px;width:480px;height:113px}
.news-thumb{position:absolute;left:0;top:0;width:186px;height:113px}
.news-title{position:absolute;left:212px;top:0;font-family:"Roboto",sans-serif;font-size:16.5px;color:var(--ink)}
.news-date{position:absolute;left:212px;top:30px;font-family:"Roboto",sans-serif;font-size:14px;color:var(--red-date);font-weight:500}
.news-body{position:absolute;left:212px;top:56px;width:265px;font-size:11px;line-height:20px}
.trade{left:625px;top:1870px;width:476px;height:327px;border:1px solid #ddd;background:#fff}
.trade-head{height:55px;background:linear-gradient(#fff,#eee);border-bottom:1px solid #ddd;text-align:center;line-height:55px;font-family:"Roboto",sans-serif;font-size:15.5px;color:var(--maroon)}
.trade-map{position:absolute;left:20px;top:58px;width:436px;height:170px;background:linear-gradient(120deg,#c9332a 0%,#2a74c2 30%,#e8782a 55%,#2a74c2 75%,#8bb33a 100%);opacity:.9;border-radius:40px 60px 30px 50px}
.legend{position:absolute;top:250px;width:74px;height:74px;border-radius:50%;color:#fff;font-size:12px;text-align:center;line-height:74px}

/* footer */
.site-footer{left:0;top:2243px;width:1200px;height:147px;background:var(--footer)}
.social{left:0;width:1200px;top:2270px;display:flex;justify-content:center;gap:11px}
.social span{width:26px;height:26px;border-radius:50%;background:#999}
.foot-nav{left:0;width:1200px;top:2318px;text-align:center;font-family:"Roboto",sans-serif;font-size:11.5px;color:#fff;word-spacing:2px}
.foot-nav i{font-style:normal;margin:0 11px;color:#ccc}
.copyright{left:0;width:1200px;top:2345px;text-align:center;font-size:11.5px;color:#fff}
</style>
</head>
<body>

<header class="site-header abs">
  <div class="brand abs"><span class="brand-dot"></span><span class="brand-name">Quillbrookes</span></div>
  <nav class="main-nav abs">
    <span class="active">HOME</span><span>FOUNDER</span><span>CONSULTANCY</span><span>SYSTEM</span><span>CASE STUDIES</span><span>CONTACT</span>
  </nav>
</header>

<section class="hero abs" role="img" aria-label="City skyline along the waterfront at dusk"></section>
<svg class="hero-arrow abs" style="left:45px;top:346px" width="34" height="66"><polyline points="32,2 2,33 32,64" fill="none" stroke="#fff" stroke-width="2"/></svg>
<svg class="hero-arrow abs" style="left:1130px;top:346px" width="34" height="66"><polyline points="2,2 32,33 2,64" fill="none" stroke="#fff" stroke-width="2"/></svg>
<h1 class="hero-title abs">QUILLBROOKES CONSULTANCY</h1>
<p class="hero-sub abs">Limited capitalizes on synergies arising..</p>

<section class="panel panel-left abs">
  <svg class="panel-icon" style="left:99px" width="62" height="54" viewBox="0 0 62 54" fill="none" stroke="#fff" stroke-width="2">
    <polyline points="2,2 2,52 60,52"/>
    <rect x="10" y="34" width="6" height="16"/><rect x="22" y="26" width="6" height="24"/><rect x="34" y="30" width="6" height="20"/><rect x="46" y="20" width="6" height="30"/>
    <circle cx="40" cy="12" r="9"/><text x="36" y="16" font-size="11" fill="#fff" stroke="none" font-family="Roboto,sans-serif">$</text>
  </svg>
  <h3>Plain Vanilla<br>Financing Solutions</h3>
  <p>The Consultancy provides access to local/regional banks across Hong Kong, Singapore, Dubai New York and London and helps corporate clients in diversifying their financial partners and adding new banks to their bank group. The Consultancy provides Trade finance solutions for working capital requirements and assists</p>
</section>
<section class="panel panel-right abs">
  <svg class="panel-icon" style="left:74px" width="56" height="50" viewBox="0 0 56 50" fill="none" stroke="#fff" stroke-width="2">
    <rect x="2" y="2" width="52" height="36" rx="2"/><line x1="20" y1="46" x2="36" y2="46"/><line x1="28" y1="38" x2="28" y2="46"/>
    <polyline points="8,28 18,20 26,26 36,12 48,18"/>
  </svg>
  <h3>Structured<br>Financing Solutions</h3>
  <p>The Consultancy provides end-to-end structured solutions on the Payables, Receivables or Inventory side for working capital requirements with off/part/on recourse balance sheet structures. We also specialize in providing credit enhancements through private or sovereign Insurance market</p>
</section>
<div class="center-badge abs"></div>

<div class="video abs" role="img" aria-label="Video still of a speaker at a podium at a business conference"></div>
<div class="play abs"><svg width="52" height="34"><polygon points="21,10 33,17 21,24" fill="#fff"/></svg></div>
<h2 class="welcome-title abs">WELCOME TO <span>QUILLBROOKES</span></h2>
<div class="welcome-text abs">
  <p>Quillbrookes Consultancy Limited capitalizes on synergies arising from trade and investment linkages between countries and knowledge of traditional and non-traditional pools of liquidity to provide consultancy services to Emerging country banks, Corporates and SMEs. The Consultancy provides bank neutral views to Corporates and SMEs in Asian emerging markets and helps in improving financial structure and efficient use of funds.</p>
  <p>Our endeavor is to provide a distinct bottom line advantage to our clients. The primary focus is in regionalisation of the banking relationship across the globe, providing structured finance solutions and off balance sheet solutions.</p>
  <p>The consultancy for the Banks and Non Banking Financial Institutions is focused on risk mitigation techniques, Export Credit Agency business and trade origination and distribution strategies along with raising long term liabilities.</p>
</div>

<section class="cases abs"></section>
<h2 class="cases-title abs">CASE STUDIES</h2>
<p class="cases-intro abs">Some of the deals completed by QCL are summarised below to describe the range of activities undertaken with Corporates veniam, quis nostrud exercitation ullamco laboris nisi ut aliquip ex ea commodo consequat. Duis aute irure</p>
<svg class="case-arrow abs" style="left:38px" width="30" height="60"><polyline points="28,2 2,30 28,58" fill="none" stroke="#ccc" stroke-width="2"/></svg>
<svg class="case-arrow abs" style="left:1132px" width="30" height="60"><polyline points="2,2 28,30 2,58" fill="none" stroke="#ccc" stroke-width="2"/></svg>
<article class="case abs" style="left:99px;background:linear-gradient(135deg,#bfc3c7,#4a4e55 60%,#222)" role="img" aria-label="Businessman touching a screen of gears">
  <span class="case-label">Export Credit..</span><span class="case-tag">Lorem ipsum dolor sit amet</span></article>
<article class="case abs" style="left:352px;background:linear-gradient(135deg,#9fc4d8,#6c94ad 50%,#c8dbe5)" role="img" aria-label="Man looking through a magnifying glass">
  <span class="case-label">Introducing Regional</span><span class="case-tag">Lorem ipsum dolor sit amet</span></article>
<article class="case abs" style="left:606px;background:linear-gradient(160deg,#dfe6ec,#a9b6c2 55%,#7d8c98)" role="img" aria-label="Figures climbing a rising red arrow over a city">
  <span class="case-label">Structured Financing</span><span class="case-tag">Lorem ipsum dolor sit amet</span></article>
<article class="case abs" style="left:858px;background:linear-gradient(135deg,#c98a2a,#5a3a1e 50%,#1f2a3a)" role="img" aria-label="Hand holding glowing network of people">
  <span class="case-label">Bank Lines Business</span><span class="case-tag">Lorem ipsum dolor sit amet</span></article>

<h2 class="news-head abs"><span class="news-dot"></span>LATEST NEWS</h2>
<article class="news-item abs" style="top:1919px">
  <div class="news-thumb" style="background:linear-gradient(135deg,#2a3550,#5b6a88 50%,#1a2238)" role="img" aria-label="Business handshake"></div>
  <h3 class="news-title">Nulla at diam ornare, aliquam urna</h3>
  <div class="news-date">JULY 25, 2015</div>
  <p class="news-body">Nulla at diam ornare, aliquam urna vel, commodo urna. Nam id risus a est luctus consectetur quis eget libero. Suspendisse potenti.</p>
</article>
<article class="news-item abs" style="top:2066px">
  <div class="news-thumb" style="background:linear-gradient(135deg,#1e3a4a,#4d7d8f 50%,#18303c)" role="img" aria-label="Hand touching a digital world map"></div>
  <h3 class="news-title">Nulla at diam ornare, aliquam urna</h3>
  <div class="news-date">JULY 25, 2015</div>
  <p class="news-body">Nulla at diam ornare, aliquam urna vel, commodo urna. Nam id risus a est luctus consectetur quis eget libero. Suspendisse potenti.</p>
</article>

<aside class="trade abs">
  <div class="trade-head">World Merchandising Trade 2012 ( USD Billion)</div>
  <div class="trade-map" role="img" aria-label="World map coloured by merchandise trade value"></div>
  <span class="legend" style="left:77px;background:#1f86cc">0-250</span>
  <span class="legend" style="left:161px;background:#86b236">250-500</span>
  <span class="legend" style="left:245px;background:#e8782a">500-1000</span>
  <span class="legend" style="left:329px;background:#b0222a">&gt;1000</span>
</aside>

<footer class="site-footer abs"></footer>
<div class="social abs"><span></span><span></span><span></span><span></span><span></span></div>
<nav class="foot-nav abs">HOME<i>/</i>FOUNDER<i>/</i>CONSULTANCY<i>/</i>SYSTEM<i>/</i>CASE STUDIES<i>/</i>CONTACT US</nav>
<p class="copyright abs">2016 © Copyrights Quillbrookes.All Rights Reserved</p>

</body>
</html>
```